Brindle Healthcare Coming Soon Sign

I need a large (10 x5) road banner announcing the construction of our new medical practice at 5187 Larkmoor Road in John's Island. The name of our practice is Brindle Healthcare and we thought it would be fund to nick name it the "Brindle Waystation". We'd like the tagline to read - "There's nothing healthy about driving an hour to see your doctor. So we're coming to you." Opening Late 2025 I have attached three logos as we have two other practices (Brindle Urgent and Brindle Aesthetics ) that should be present on the bottom of the sign but the main business is Brindle Healthcare. For more information on our look/feel visit our website www.goplainway-example.com (which should be somewhere on the banner as well)
Updates

The signage needs to say Coming Late Fall 2025!

Target Market(s)

Drive By traffic must be made aware that we are coming soon

Industry/Entity Type

Healthcare

Requirements
Nice to have
• Western Theme

```html
<!DOCTYPE html>
<html lang="en">
<head>
<meta charset="utf-8">
<title>Brindle Waystation Road Banner</title>
<link rel="stylesheet" href="https://fonts.googleapis.com/css2?family=Montserrat:wght@600;700&display=swap">
<style>
  :root {
    --navy: #1f3865;
    --sky: #5fb0d0;
    --pink: #e6207a;
    --red: #e8403a;
    --frame-deep: #2a56a4;
    --frame-teal: #62b2b8;
    --mist: #d7eaf3;
    --mist-light: #eef6fa;
    --paper: #ffffff;
    --ink: #111a2c;
  }
  * { margin: 0; padding: 0; box-sizing: border-box; }
  html, body {
    width: 1200px; height: 1200px; overflow: hidden;
    background: var(--paper);
    font-family: "Montserrat", Arial, sans-serif;
    color: var(--navy);
  }
  .banner { position: absolute; left: 119px; width: 967px; height: 483px; }
  .banner--photo { top: 77px; }
  .banner--light { top: 654px; }
  .banner__art { position: absolute; inset: 0; width: 100%; height: 100%; }

  .masthead {
    position: absolute; top: 48px; left: 0; right: 0;
    display: flex; justify-content: center; align-items: center; gap: 29px;
  }
  .masthead__mark { width: 100px; height: 92px; background: var(--sky); border: 5px solid var(--navy); border-radius: 6px; }
  .masthead__name { font-weight: 700; line-height: 1; }
  .masthead__line1 { display: block; font-size: 62px; letter-spacing: 0.12em; color: var(--navy); }
  .masthead__line2 { display: block; font-size: 30px; letter-spacing: 0.26em; margin-top: 12px; color: var(--sky); }

  .rule { position: absolute; left: 56px; width: 857px; height: 2px; background: var(--navy); }
  .rule--top { top: 181px; }
  .rule--bottom { top: 299px; }

  .tagline {
    position: absolute; top: 199px; left: 40px; right: 40px;
    text-align: center; font-weight: 700; font-size: 21px;
    letter-spacing: 0.12em; line-height: 42px; color: var(--navy);
  }

  .opening {
    position: absolute; top: 318px; left: 0; right: 0;
    text-align: center; font-weight: 700; font-size: 22px;
    letter-spacing: 0.24em; color: var(--sky);
  }

  .family { position: absolute; top: 362px; left: 0; right: 0; height: 40px; }
  .family__brand {
    position: absolute; top: 0; display: flex; align-items: center; gap: 10px;
    transform: translateX(-50%); font-weight: 700; line-height: 1;
  }
  .family__brand--health { left: 251px; color: var(--navy); }
  .family__brand--aesth { left: 484px; color: var(--pink); }
  .family__brand--urgent { left: 718px; color: var(--red); }
  .family__mark { width: 32px; height: 32px; }
  .family__brand--health .family__mark { background: var(--sky); }
  .family__brand--aesth .family__mark { background: var(--pink); }
  .family__brand--urgent .family__mark { background: var(--red); }
  .family__word1 { display: block; font-size: 22px; letter-spacing: 0.14em; }
  .family__word2 { display: block; font-size: 11px; letter-spacing: 0.24em; margin-top: 5px; }

  .address {
    position: absolute; top: 429px; left: 0; right: 0;
    text-align: center; font-weight: 600; font-size: 16px;
    letter-spacing: 0.1em; color: var(--ink);
  }
</style>
</head>
<body>

<section class="banner banner--photo">
  <svg class="banner__art" viewBox="0 0 967 483" role="img" aria-label="Textured blue border around a bright hospital corridor photograph">
    <defs>
      <linearGradient id="edgeTone" x1="0" y1="0" x2="0.3" y2="1">
        <stop offset="0" stop-color="var(--frame-teal)"/>
        <stop offset="0.5" stop-color="var(--frame-deep)"/>
        <stop offset="1" stop-color="#24498f"/>
      </linearGradient>
      <radialGradient id="hallTone" cx="0.5" cy="0.6" r="0.6">
        <stop offset="0" stop-color="#f6fbfd"/>
        <stop offset="0.6" stop-color="var(--mist)"/>
        <stop offset="1" stop-color="#b9dbea"/>
      </radialGradient>
    </defs>
    <rect width="967" height="483" fill="url(#edgeTone)"/>
    <path d="M91 21 H876 A70 70 0 0 0 946 91 V391 A70 70 0 0 0 876 461 H91 A70 70 0 0 0 21 391 V91 A70 70 0 0 0 91 21 Z"
          fill="url(#hallTone)" stroke="var(--navy)" stroke-width="3.5"/>
  </svg>
  <div class="masthead">
    <span class="masthead__mark"></span>
    <span class="masthead__name">
      <span class="masthead__line1">BRINDLE</span>
      <span class="masthead__line2">WAYSTATION</span>
    </span>
  </div>
  <div class="rule rule--top"></div>
  <p class="tagline">THERE'S NOTHING HEALTHY ABOUT DRIVING AN HOUR<br>TO SEE YOUR DOCTOR. SO WE'RE COMING TO YOU.</p>
  <div class="rule rule--bottom"></div>
  <p class="opening">COMING LATE FALL 2025</p>
  <div class="family">
    <div class="family__brand family__brand--health"><span class="family__mark"></span><span><span class="family__word1">BRINDLE</span><span class="family__word2">HEALTHCARE</span></span></div>
    <div class="family__brand family__brand--aesth"><span class="family__mark"></span><span><span class="family__word1">BRINDLE</span><span class="family__word2">AESTHETICS</span></span></div>
    <div class="family__brand family__brand--urgent"><span class="family__mark"></span><span><span class="family__word1">BRINDLE</span><span class="family__word2">URGENT</span></span></div>
  </div>
  <p class="address">5187 Larkmoor Road, John's Island &nbsp;·&nbsp; www.goplainway-example.com</p>
</section>

<section class="banner banner--light">
  <svg class="banner__art" viewBox="0 0 967 483" role="img" aria-label="Faint pale hospital corridor photograph behind a white panel">
    <defs>
      <linearGradient id="paleTone" x1="0" y1="0" x2="1" y2="1">
        <stop offset="0" stop-color="var(--mist)"/>
        <stop offset="0.5" stop-color="var(--mist-light)"/>
        <stop offset="1" stop-color="var(--mist)"/>
      </linearGradient>
    </defs>
    <rect width="967" height="483" fill="url(#paleTone)"/>
    <path d="M91 21 H876 A70 70 0 0 0 946 91 V391 A70 70 0 0 0 876 461 H91 A70 70 0 0 0 21 391 V91 A70 70 0 0 0 91 21 Z"
          fill="var(--paper)" stroke="var(--navy)" stroke-width="3.5"/>
  </svg>
  <div class="masthead">
    <span class="masthead__mark"></span>
    <span class="masthead__name">
      <span class="masthead__line1">BRINDLE</span>
      <span class="masthead__line2">WAYSTATION</span>
    </span>
  </div>
  <div class="rule rule--top"></div>
  <p class="tagline">THERE'S NOTHING HEALTHY ABOUT DRIVING AN HOUR<br>TO SEE YOUR DOCTOR. SO WE'RE COMING TO YOU.</p>
  <div class="rule rule--bottom"></div>
  <p class="opening">COMING LATE FALL 2025</p>
  <div class="family">
    <div class="family__brand family__brand--health"><span class="family__mark"></span><span><span class="family__word1">BRINDLE</span><span class="family__word2">HEALTHCARE</span></span></div>
    <div class="family__brand family__brand--aesth"><span class="family__mark"></span><span><span class="family__word1">BRINDLE</span><span class="family__word2">AESTHETICS</span></span></div>
    <div class="family__brand family__brand--urgent"><span class="family__mark"></span><span><span class="family__word1">BRINDLE</span><span class="family__word2">URGENT</span></span></div>
  </div>
  <p class="address">5187 Larkmoor Road, John's Island &nbsp;·&nbsp; www.goplainway-example.com</p>
</section>

</body>
</html>
```